Dynamic Business Card for Sports Supplements Company

Hi! I'm looking for an awesome business card to match my existing sports supplement company. I have uploaded my current company logo and screenshot of the front page of my website.

I would like to have something dynamic and interesting and utilize the colors in the website - the reds and purples

The business card should be double sided and focus on a unique eye-catching design on the back and include all the relevant company info.

Most importantly, it should say somewhere: "Sign up on our website for a coupon code."

Target Market(s)

Mostly for women gym goers but it shouldn't be too feminine. It should be in keeping with the website design. It should flow and clearly be connected to it

Industry/Entity Type

Business

Contact Information for Business Card

Lorraine K. Vestal
CEO
LVestal@Quorvanexco.com
www.quorvanexco.com
555.417.3820
P.O. Box 47315
Burke, Virginia 00000

Sign up on our website for a coupon code

Font styles to use
Serif
Sans Serif
Other font styles liked:
• Novecento font family and "Quorvanex" is in AR Destine font

Requirements
Must have
• One side should be a bold Quorvanex logo design. Even just the symbol itself may be o.k. (see attached file)

```html
<!DOCTYPE html>
<html lang="en">
<head>
<meta charset="utf-8">
<title>Quorvanex Business Card</title>
<link href="https://fonts.googleapis.com/css2?family=Source+Sans+3:ital,wght@0,400;0,600;0,700;1,400&display=swap" rel="stylesheet">
<style>
  :root {
    --backdrop: #e7e4df;
    --card: #000000;
    --red: #e8202a;
    --white: #ffffff;
    --soft: #d8d8d8;
    --muted: #8a8a8a;
    --rule: #3a3a3a;
  }
  * { margin: 0; padding: 0; box-sizing: border-box; }
  html, body {
    width: 1200px; height: 987px; overflow: hidden;
    background: var(--backdrop);
    font-family: "Source Sans 3", Arial, sans-serif;
  }
  .card {
    position: absolute; left: 293px; width: 615px; height: 350px;
    background: var(--card);
    box-shadow: 0 3px 10px rgba(0,0,0,.35);
  }
  .card--front { top: 130px; }
  .card--back { top: 506px; }

  .brand {
    position: absolute; left: 40px; width: 250px; top: 110px;
    text-align: center;
  }
  .brand__mark {
    width: 26px; height: 26px; background: var(--red);
    margin: 0 auto 16px;
  }
  .brand__name {
    color: var(--white); font-weight: 700; font-size: 31px;
    letter-spacing: 1px; text-transform: uppercase; line-height: 1;
  }
  .brand__tagline {
    color: var(--muted); font-size: 8.5px; letter-spacing: 2.2px;
    text-transform: uppercase; margin-top: 5px;
  }

  .divider {
    position: absolute; left: 297px; top: 87px; width: 1px; height: 187px;
    background: var(--rule);
  }

  .contact { position: absolute; left: 321px; top: 84px; color: var(--soft); }
  .contact__name {
    color: var(--red); font-size: 21px; font-weight: 600;
    text-transform: uppercase; letter-spacing: .3px; line-height: 1;
  }
  .contact__title { font-size: 16px; margin: 5px 0 0 2px; line-height: 1.1; }
  .contact__address { font-size: 16px; margin: 16px 0 0 2px; line-height: 23px; }
  .contact__list { list-style: none; margin: 6px 0 0 2px; font-size: 16px; line-height: 23px; }
  .contact__list li { display: flex; align-items: center; }
  .contact__list svg { width: 13px; height: 13px; margin-right: 9px; fill: var(--red); flex: none; }

  .back-brand {
    position: absolute; left: 0; right: 0; top: 118px;
    display: flex; align-items: center; justify-content: center; gap: 18px;
  }
  .back-brand__mark { width: 52px; height: 52px; background: var(--red); }
  .back-brand__name {
    color: var(--white); font-weight: 700; font-size: 60px;
    text-transform: uppercase; letter-spacing: 2px; line-height: 1;
  }
  .back-note {
    position: absolute; left: 0; right: 0; top: 288px; text-align: center;
    color: var(--white); font-style: italic; font-size: 16px;
  }
</style>
</head>
<body>
  <section class="card card--front">
    <div class="brand">
      <div class="brand__mark"></div>
      <div class="brand__name">Quorvanex</div>
      <div class="brand__tagline">Strength In Every Rep</div>
    </div>
    <div class="divider"></div>
    <div class="contact">
      <div class="contact__name">Lorraine K. Vestal</div>
      <div class="contact__title">CEO</div>
      <div class="contact__address">P.O. Box 47315<br>Alder Falls, Oregon 00000</div>
      <ul class="contact__list">
        <li><svg viewBox="0 0 24 24"><path d="M6.6 10.8a15.1 15.1 0 0 0 6.6 6.6l2.2-2.2c.3-.3.7-.4 1-.2 1.1.4 2.3.6 3.6.6.6 0 1 .4 1 1V20c0 .6-.4 1-1 1A17 17 0 0 1 3 4c0-.6.4-1 1-1h3.5c.6 0 1 .4 1 1 0 1.3.2 2.5.6 3.6.1.3 0 .7-.2 1z"/></svg>555.417.3820</li>
        <li><svg viewBox="0 0 24 24"><path d="M2 5h20v2l-10 6L2 7zM2 9l10 6 10-6v10H2z"/></svg>LVestal@Quorvanexco.com</li>
        <li><svg viewBox="0 0 24 24"><path d="M12 2a10 10 0 1 0 0 20 10 10 0 0 0 0-20zm-1 17.9A8 8 0 0 1 4 12l5 5v1a2 2 0 0 0 2 2zm6.9-2.5A2 2 0 0 0 16 16h-1v-3a1 1 0 0 0-1-1H8v-2h2a1 1 0 0 0 1-1V7h2a2 2 0 0 0 2-2v-.4a8 8 0 0 1 2.9 12.8z"/></svg>www.quorvanexco.com</li>
      </ul>
    </div>
  </section>

  <section class="card card--back">
    <div class="back-brand">
      <div class="back-brand__mark"></div>
      <div class="back-brand__name">Quorvanex</div>
    </div>
    <p class="back-note">Sign up on our website for a coupon code</p>
  </section>
</body>
</html>
```